Medical Practice needs a Letterhead Design

We need a clean, modern letterhead design for our stem cell medical practice.

Industry/Entity Type

Medical

```html
<!DOCTYPE html>
<html lang="en">
<head>
<meta charset="utf-8">
<title>Nuvara Medical Letterhead</title>
<link href="https://fonts.googleapis.com/css2?family=Arimo:wght@400&display=swap" rel="stylesheet">
<style>
  :root {
    --navy: #0f3347;
    --lime: #b5c935;
    --mist: #e6e8eb;
    --paper: #ffffff;
    --motif-grey: rgba(196, 197, 204, 0.45);
    --motif-green: rgba(232, 236, 204, 0.9);
  }
  * { margin: 0; padding: 0; box-sizing: border-box; }
  html, body {
    width: 1200px;
    height: 800px;
    overflow: hidden;
    background: var(--mist);
  }
  .canvas {
    position: relative;
    width: 1200px;
    height: 800px;
  }
  .letterhead {
    position: absolute;
    left: 343px;
    top: 47px;
    width: 514px;
    height: 706px;
    background: var(--paper);
    overflow: hidden;
    font-family: "Arimo", Arial, sans-serif;
    color: var(--navy);
  }
  .top-band {
    position: absolute;
    top: 0;
    left: 0;
    width: 100%;
    height: 15px;
    display: flex;
  }
  .top-band__navy { width: 65%; background: var(--navy); }
  .top-band__lime { flex: 1; background: var(--lime); }
  .brand {
    position: absolute;
    top: 74px;
    right: 16px;
    display: flex;
    align-items: center;
    gap: 7px;
  }
  .brand__dot {
    width: 10px;
    height: 10px;
    border-radius: 50%;
    background: var(--lime);
  }
  .brand__name {
    font-size: 22px;
    font-weight: 400;
    line-height: 1;
    color: var(--navy);
  }
  .corner-motif {
    position: absolute;
    left: 0;
    bottom: 0;
    width: 340px;
    height: 330px;
    background:
      radial-gradient(ellipse 120px 70px at 45% 22%, var(--motif-grey) 0%, rgba(196,197,204,0) 100%),
      radial-gradient(ellipse 170px 140px at 40% 62%, var(--motif-green) 0%, rgba(238,240,217,0.45) 55%, rgba(255,255,255,0) 100%);
  }
  .contact {
    position: absolute;
    right: 16px;
    bottom: 26px;
    text-align: right;
    font-style: normal;
    font-size: 8.5px;
    line-height: 9.8px;
    color: var(--navy);
  }
</style>
</head>
<body>
  <div class="canvas">
    <div class="letterhead">
      <div class="top-band">
        <div class="top-band__navy"></div>
        <div class="top-band__lime"></div>
      </div>

      <div class="brand">
        <span class="brand__dot"></span>
        <span class="brand__name">Nuvara Medical</span>
      </div>

      <div class="corner-motif" role="img" aria-label="Soft decorative motif of an arc of grey dots above a pale green leaf curve"></div>

      <address class="contact">
        <div>Address line 1</div>
        <div>Tel:00 00 0000 0000 Fax : 00000000 Mobile :00 00000 00000</div>
        <div>Email: hello@nuvaramedical.com Website:www.nuvaramedical.com</div>
      </address>
    </div>
  </div>
</body>
</html>
```